New hardcover book cover

I want a striking, eye-catching cover with title, subtitle and a picture.See for previous book covers: www.brightquillpress.com

Target Market(s)

young, successful entrepreneurs that have built a business in a niche market that they discovered.

Font styles to use
Serif

Colors

Designer to choose colors to be used in the design.

Requirements
Must have
• A book cover that impresses and captures the imagination of those who look at it.
• MY MISTAKE, SORRY.
• Title: Founders Behind the Quiet Trade Boom
• Subtitle: 25 stories of success from
• discovering hidden opportunities
• Author: Dennis Harlow
• Please use the photo attached, thanks.

```html
<!DOCTYPE html>
<html lang="en">
<head>
<meta charset="utf-8">
<title>Founders Behind the Quiet Trade Boom — Cover</title>
<link rel="stylesheet" href="https://fonts.googleapis.com/css2?family=Josefin+Sans:wght@300;400&family=Montserrat:wght@800;900&display=swap">
<style>
  :root {
    --backdrop: #1c1c1e;
    --cover-dark: #25252d;
    --target-red: #c2385e;
    --steel: #5b6272;
    --sky: #a9c6dc;
    --text-white: #ffffff;
  }
  * { margin: 0; padding: 0; box-sizing: border-box; }
  html, body {
    width: 1200px;
    height: 905px;
    overflow: hidden;
    background: var(--backdrop);
  }
  .canvas {
    position: relative;
    width: 1200px;
    height: 905px;
  }
  .cover {
    position: absolute;
    left: 320px;
    top: 27px;
    width: 560px;
    height: 850px;
    overflow: hidden;
    background: var(--cover-dark);
  }
  .cover-photo {
    position: absolute;
    inset: 0;
    background: linear-gradient(100deg, var(--target-red) 0%, #8d2f52 28%, var(--cover-dark) 45%, var(--steel) 68%, var(--sky) 100%);
  }
  .cover-shade {
    position: absolute;
    inset: 0;
    background: linear-gradient(180deg, rgba(30,30,38,0.55) 0%, rgba(30,30,38,0) 20%, rgba(30,30,38,0) 50%, rgba(30,30,38,0.85) 75%, rgba(30,30,38,0.95) 100%);
  }
  .author {
    position: absolute;
    top: 62px;
    left: 0;
    right: 0;
    text-align: center;
    font-family: "Josefin Sans", sans-serif;
    font-weight: 300;
    font-size: 38px;
    letter-spacing: 0.12em;
    color: var(--text-white);
    text-transform: uppercase;
  }
  .title {
    position: absolute;
    top: 520px;
    left: 0;
    right: 0;
    text-align: center;
    font-family: "Montserrat", sans-serif;
    font-weight: 900;
    color: var(--text-white);
    text-transform: uppercase;
    line-height: 1;
    letter-spacing: -0.02em;
  }
  .title-line { display: block; }
  .title-lead { font-size: 40px; }
  .title-row {
    display: flex;
    justify-content: center;
    align-items: center;
    gap: 8px;
    margin-top: 4px;
  }
  .title-connector {
    display: flex;
    flex-direction: column;
    font-size: 18px;
    line-height: 0.95;
    text-align: right;
  }
  .title-key { font-size: 50px; }
  .title-framed {
    display: flex;
    justify-content: center;
    align-items: center;
    gap: 14px;
    font-size: 50px;
    margin-top: 2px;
  }
  .title-dash {
    width: 44px;
    height: 5px;
    background: var(--text-white);
  }
  .title-finale { font-size: 68px; margin-top: 6px; }
  .subtitle {
    position: absolute;
    top: 768px;
    left: 0;
    right: 0;
    text-align: center;
    font-family: "Josefin Sans", sans-serif;
    font-weight: 400;
    font-size: 18px;
    line-height: 1.35;
    color: var(--text-white);
    text-transform: uppercase;
  }
</style>
</head>
<body>
  <div class="canvas">
    <section class="cover">
      <div class="cover-photo" role="img" aria-label="Close-up photograph of a dart striking the red centre of an archery target against a blue sky"></div>
      <div class="cover-shade"></div>
      <p class="author">Dennis Harlow</p>
      <h1 class="title">
        <span class="title-line title-lead">Founders</span>
        <span class="title-row">
          <span class="title-connector"><span>Behind</span><span>the</span></span>
          <span class="title-key">Quiet</span>
        </span>
        <span class="title-framed">
          <span class="title-dash"></span>
          <span>Trade</span>
          <span class="title-dash"></span>
        </span>
        <span class="title-line title-finale">Boom</span>
      </h1>
      <p class="subtitle">25 captivating stories of success<br>from discovering hidden opportunities</p>
    </section>
  </div>
</body>
</html>
```